Larkspur Energy - Stock Certificate

We need a custom designed stock certificate that represents the look of our company logo but also have a cool look compared to a standard stock certificate. We thinking we want the logo in gold. Our website is https://www.larkspurenergyusa.example.

We are wanting the certificate to look very professional and really cool, we have sales agents that work for the company and we are creating a program by which the sales agents can gain ownership in the company. So the certificates need to have a very cool appeal and that provides a sense of pride in owning "Units" in Larkspur Energy.

Reason: Extending so other board members can vote as well, thank you all!

Target Market(s)

Stock/Shareholders

Industry/Entity Type

It Company

Font styles to use
Script

Requirements
Must have
• Must look like a stock certificate, must use our logo which the psd file for it was attached.
Nice to have
• Nice to have the logo in gold

```html
<!DOCTYPE html>
<html lang="en">
<head>
<meta charset="utf-8">
<title>Larkspur Energy – Stock Certificate</title>
<link rel="stylesheet" href="https://fonts.googleapis.com/css2?family=Felipa&family=Montserrat:wght@500&display=swap">
<style>
  :root {
    --paper: #bca88e;
    --border-tone: #5a5047;
    --border-edge: #2b2825;
    --band-black: #242322;
    --band-bronze: #a87e55;
    --seal-dark: #1e1d1c;
    --gold: #d9a441;
    --ink: #171412;
    --title: #ffffff;
  }
  html, body {
    margin: 0;
    padding: 0;
    width: 1200px;
    height: 927px;
    overflow: hidden;
    background: var(--paper);
  }
  .certificate {
    display: block;
    width: 1200px;
    height: 927px;
  }
  .paper { fill: var(--paper); }
  .border-pattern { fill: var(--border-tone); }
  .border-edge { fill: none; stroke: var(--border-edge); stroke-width: 2; }
  .band-bronze { fill: var(--band-bronze); }
  .band-black { fill: var(--band-black); }
  .seal-ring { fill: var(--band-bronze); }
  .seal-core { fill: var(--seal-dark); }
  .seal-name {
    font-family: "Montserrat", sans-serif;
    font-weight: 500;
    font-size: 17px;
    fill: var(--gold);
    letter-spacing: 1px;
  }
  .title {
    font-family: "Felipa", cursive;
    font-size: 88px;
    fill: var(--title);
  }
  .copy {
    font-family: "Felipa", cursive;
    font-size: 37px;
    fill: var(--ink);
  }
  .fill-line { stroke: var(--ink); stroke-width: 2.2; }
</style>
</head>
<body>
<svg class="certificate" viewBox="0 0 1200 927" xmlns="http://www.w3.org/2000/svg">
  <rect class="paper" x="0" y="0" width="1200" height="927"/>

  <g class="frame">
    <path class="border-pattern" role="img" aria-label="Decorative zigzag and dotted border pattern"
          fill-rule="evenodd"
          d="M0 0H1200V927H0Z M35 37V889H1164V37Z"/>
    <rect class="border-edge" x="35" y="37" width="1129" height="852"/>
  </g>

  <g class="header-band">
    <rect class="band-bronze" x="35" y="116" width="1129" height="145"/>
    <rect class="band-black" x="35" y="131" width="1129" height="112"/>
  </g>

  <g class="seal">
    <circle class="seal-ring" cx="273" cy="181" r="107"/>
    <circle class="seal-core" cx="273" cy="181" r="93"/>
    <text class="seal-name" x="273" y="187" text-anchor="middle">Larkspur Energy</text>
  </g>

  <text class="title" x="436" y="217">stock certificate</text>

  <g class="form">
    <text class="copy" x="658" y="315" text-anchor="middle">This is to certify that</text>
    <line class="fill-line" x1="118" y1="383" x2="1129" y2="383"/>

    <text class="copy" x="100" y="487">Is the owner of</text>
    <line class="fill-line" x1="355" y1="494" x2="616" y2="494"/>
    <text class="copy" x="633" y="487">shares of stock of</text>
    <line class="fill-line" x1="892" y1="494" x2="1129" y2="494"/>

    <line class="fill-line" x1="99" y1="576" x2="549" y2="576"/>
    <text class="copy" x="565" y="570">on the</text>
    <line class="fill-line" x1="667" y1="576" x2="1010" y2="576"/>
    <text class="copy" x="1026" y="570">day of</text>

    <line class="fill-line" x1="97" y1="669" x2="309" y2="669"/>
    <text class="copy" x="313" y="666">In the year</text>
    <line class="fill-line" x1="515" y1="669" x2="674" y2="669"/>
    <text class="copy" x="686" y="666">At</text>
    <line class="fill-line" x1="749" y1="669" x2="1120" y2="669"/>
    <text class="copy" x="1122" y="666">.</text>

    <text class="copy" x="675" y="751">Signed,</text>
    <line class="fill-line" x1="813" y1="759" x2="1131" y2="759"/>

    <text class="copy" x="680" y="830">Signed,</text>
    <line class="fill-line" x1="818" y1="838" x2="1135" y2="838"/>
  </g>
</svg>
</body>
</html>
```